Dental Practice Billboard Design

We are a newer dental practice in need of a simple but appealing billboard for our growing dental practice to attract new patients. The practice is owned by husband and wife dentists and is family friendly in a small town in Kentucky. We try to be very friendly and caring to our patients. Would prefer a blue background for the billboard and our tooth logo to be prominent. We are partial to the Patua One font used in the image below but please feel free to tweak it as you deem necessary. The shape of the uppercase D and lowercase g are why we like that font, so fonts with a similarly shaped “D” and “g” would work as well. Please include our phone number (555) 847-1390. Please see our website Harlowbrookdentistry.example for more info on the practice if needed. Thank you! Looking forward to seeing your creation.
Updates

The dimensions will be 12ft x 24ft (3.6576m x 7.3152m). Apologies for not including this in the original prompt. Thank you all for your submissions.

Industry/Entity Type

Dental

Font styles to use
Other font styles liked:
• Patua One

Colors
0054AA
0677BA
7BADD7
CADEEF
E8F1F8
0094D4
00A9DD
6FCCEA
C7EBF8
E9F6FB
00AB8E
00BBA5
67D7C9
C6EFE9
E9F9F6
59FF00
82FF00
B8FF75
E3FFCB
F4FFEA

Requirements
Must have
• Phone number, website, Logo, Practice name “Harlow Brook Dentistry”
Should not have
• A tagline or slogan

```html
<!DOCTYPE html>
<html lang="en">
<head>
<meta charset="UTF-8">
<title>Harlow Brook Dentistry Billboard</title>
<link rel="stylesheet" href="https://fonts.googleapis.com/css2?family=Patua+One&family=Fira+Sans+Extra+Condensed:wght@600&display=swap">
<style>
  :root {
    --navy: #00215b;
    --green: #0aa611;
    --white: #ffffff;
  }
  * { margin: 0; padding: 0; box-sizing: border-box; }
  html, body { width: 1200px; height: 722px; overflow: hidden; background: var(--white); }
  .billboard {
    position: relative;
    width: 1200px;
    height: 722px;
    background: var(--white);
  }
  .brand-panel {
    position: absolute;
    left: 0; top: 0;
    width: 1200px; height: 585px;
    background: var(--navy);
  }
  .brand-mark {
    position: absolute;
    left: 110px; top: 165px;
    width: 250px; height: 250px;
    border-radius: 50%;
    background: var(--green);
  }
  .brand-name {
    position: absolute;
    left: 420px; top: 170px;
    font-family: "Patua One", serif;
    color: var(--white);
    line-height: 1;
  }
  .brand-name .line-main { display: block; font-size: 104px; }
  .brand-name .line-sub { display: block; font-size: 78px; margin-top: 30px; margin-left: 4px; }
  .contact-band {
    position: absolute;
    left: 0; top: 585px;
    width: 1200px; height: 105px;
    display: flex;
    align-items: center;
    padding-left: 52px;
    gap: 14px;
  }
  .contact-icon {
    width: 52px; height: 52px;
    border-radius: 50%;
    background: var(--green);
    display: flex; align-items: center; justify-content: center;
    flex-shrink: 0;
  }
  .contact-phone {
    font-family: "Fira Sans Extra Condensed", sans-serif;
    font-weight: 600;
    font-size: 62px;
    color: var(--navy);
    margin-right: 22px;
  }
  .contact-web {
    font-family: "Patua One", serif;
    font-size: 36px;
    color: var(--navy);
  }
  .accent-strip {
    position: absolute;
    left: 0; top: 690px;
    width: 1200px; height: 32px;
    background: var(--green);
  }
</style>
</head>
<body>
  <div class="billboard">
    <div class="brand-panel">
      <div class="brand-mark"></div>
      <div class="brand-name">
        <span class="line-main">Harlow Brook</span>
        <span class="line-sub">Dentistry</span>
      </div>
    </div>

    <div class="contact-band">
      <span class="contact-icon">
        <svg width="28" height="28" viewBox="0 0 24 24" aria-hidden="true">
          <path fill="#ffffff" d="M6.6 10.8c1.4 2.8 3.8 5.1 6.6 6.6l2.2-2.2c.3-.3.7-.4 1-.2 1.1.4 2.3.6 3.6.6.6 0 1 .4 1 1V20c0 .6-.4 1-1 1C10.6 21 3 13.4 3 4c0-.6.4-1 1-1h3.5c.6 0 1 .4 1 1 0 1.3.2 2.5.6 3.6.1.3 0 .7-.2 1z"/>
        </svg>
      </span>
      <span class="contact-phone">(555) 847-1390</span>
      <span class="contact-icon">
        <svg width="30" height="30" viewBox="0 0 24 24" aria-hidden="true">
          <rect x="5" y="5" width="14" height="10" rx="1" fill="none" stroke="#ffffff" stroke-width="2"/>
          <rect x="2" y="17" width="20" height="2.5" rx="1" fill="#ffffff"/>
        </svg>
      </span>
      <span class="contact-web">Harlowbrookdentistry.example</span>
    </div>

    <div class="accent-strip"></div>
  </div>
</body>
</html>
```